Custom PowerPoint Template for Training & Workshop Presentations

I am looking for a professional designer to create a custom PowerPoint template (PPTX) for my training and workshop materials. My trainings are designed for: HR professionals and Learning & Development specialists;
Executives and team leaders; Organizations investing in employee development and workplace learning; Participants in professional development workshops, seminars, and didactics trainings
The template should therefore appear trustworthy, calm, friendly, structured, and competence‑oriented. The design should be visually appealing, easy to read, and fully editable.

All branding files are attached to this project.
Please use them as the main reference for your design:
Logo (included as attachment)
Brand color specifications (included as attachment)
Font specifications related to the logo and brand (included as attachment)

What I need:
--> Title Slide: Title, subtitle, name, logo
(1–2 variations)
--> Agenda / Overview Slide
--> Content Slides
--> Text only
--> Text + image
-->Two-column
--> Section header
--> Quote / key message
--> Graphic / Model Slides: (1–2 layouts for frameworks, processes, models)
--> Tables & Charts: (Table styles in brand colors; Chart design aligned with typography and color palette)
--> Closing Slide: (Contact or call-to-action; Optional second variation)

All layouts must be built properly inside the PowerPoint Slide Master

```html
<!DOCTYPE html>
<html lang="en">
<head>
<meta charset="utf-8">
<title>Training Presentation Template Overview</title>
<link rel="stylesheet" href="https://fonts.googleapis.com/css2?family=Plus+Jakarta+Sans:wght@300;400;500;600;700;800&family=Allura&display=swap">
<style>
:root{
  --bg-top:#8a9bb3;
  --bg-bottom:#a9b6c8;
  --navy:#132b54;
  --blue:#1b5c96;
  --steel:#8ea8c0;
  --steel-light:#a9cbe8;
  --ring-grey:#c8d1db;
  --ink:#1d1d1f;
  --muted:#8a8f98;
  --panel:#f3f4f6;
  --white:#ffffff;
  --sans:"Plus Jakarta Sans", Arial, sans-serif;
  --script:"Allura", cursive;
}
*{margin:0;padding:0;box-sizing:border-box}
html,body{width:865px;height:1200px;overflow:hidden}
body{background:linear-gradient(180deg,var(--bg-top),var(--bg-bottom) 55%,var(--bg-top));font-family:var(--sans);color:var(--ink);position:relative}
.slide{position:absolute;width:383px;height:216px;background:var(--white);overflow:hidden}
.col-left{left:45px}.col-right{left:437px}
.row-1{top:42px}.row-2{top:267px}.row-3{top:492px}.row-4{top:717px}.row-5{top:942px}
.abs{position:absolute}
.photo{position:absolute;border-radius:3px}
.eyebrow{position:absolute;font-size:9.5px;font-weight:400;color:var(--ink);letter-spacing:.2px;display:flex;align-items:center;gap:6px;white-space:nowrap}
.eyebrow::after{content:"";display:block;width:36px;height:1px;background:var(--steel-light)}
.eyebrow.plain::after{display:none}
.heading{position:absolute;font-size:17px;font-weight:700;color:var(--navy);letter-spacing:-.6px;white-space:nowrap}
.body{position:absolute;font-size:6.4px;line-height:1.3;color:var(--muted);font-weight:400}
.body.dark{color:var(--ink)}
.body.bold{color:var(--ink);font-weight:600}
.body.white{color:var(--white)}
.title-sm{position:absolute;font-size:7.8px;color:var(--ink);font-weight:500;line-height:1.2}

/* brand name */
.brand{position:absolute;display:flex;align-items:center;gap:6px;color:var(--white);white-space:nowrap}
.brand-square{width:9px;height:9px;background:currentColor;border-radius:1px}
.brand-name{font-size:11px;font-weight:600;letter-spacing:-.1px}
.tagline{position:absolute;font-size:6.4px;font-weight:400;white-space:nowrap}

/* title slide */
.slide-title{background:linear-gradient(135deg,#1c6aad,#1d5f9f 60%,#1a5590)}
.script-training{position:absolute;left:26px;top:68px;font-family:var(--script);font-size:30px;color:var(--white)}
.title-line{position:absolute;left:29px;font-size:16px;font-weight:800;color:var(--white);letter-spacing:-.2px;white-space:nowrap}
.title-line .script{font-family:var(--script);font-weight:400;font-size:24px;color:#b9d4ec;margin-left:3px}
.coaching{position:absolute;left:73px;top:153px;width:104px;height:28px;background:var(--steel-light);border-radius:3px;color:var(--blue);font-weight:800;font-size:16px;display:flex;align-items:center;justify-content:center}

/* agenda */
.agenda-word{position:absolute;left:0;right:0;top:40px;text-align:center;font-size:45px;font-weight:800;letter-spacing:-1px;background:linear-gradient(180deg,#c4cbd4,#eef0f3 45%,#b7c0cb);-webkit-background-clip:text;background-clip:text;color:transparent}
.agenda-item{position:absolute;display:flex;gap:5px;font-size:9.6px;line-height:1.05;color:var(--ink);white-space:nowrap}
.agenda-item .arrow{font-size:8px;line-height:1.1}
.agenda-item .soft{font-weight:300;color:#555}
.agenda-item .strong{font-weight:500}

.card{position:absolute;border-radius:3px;padding:9px 7px}
.icon-tile{position:absolute;width:20px;height:20px;border-radius:2px;display:flex;align-items:center;justify-content:center}
.pct-pill{position:absolute;left:331px;top:74px;width:29px;height:15px;border-radius:2px;background:var(--steel);color:var(--white);font-size:8.5px;display:flex;align-items:center;justify-content:center}

.center{left:0;right:0;text-align:center}
.pill{position:absolute;left:122px;top:84px;width:138px;height:16px;border-radius:2px;background:var(--steel);color:var(--white);font-size:6.6px;display:flex;align-items:center;justify-content:center}
.feature{position:absolute;width:96px;text-align:center}
.feature .title-sm{position:static;margin-bottom:2px}
.feature .body{position:static}
.feature-dot{position:absolute;width:22px;height:22px;border-radius:50%;background:var(--blue);border:2px solid #d9e5f0;display:flex;align-items:center;justify-content:center}

.slide-break{background:linear-gradient(135deg,#1c6aad,#1d5f9f 60%,#1a5590)}

.slide-close{background:radial-gradient(circle at 50% 50%,#ffffff 20%,#eceef1 100%)}
.thanks{position:absolute;left:0;right:0;top:66px;text-align:center;font-family:var(--script);font-size:40px;color:#6f8ea8}
.contact{position:absolute;display:flex;gap:6px;font-size:7.4px;line-height:1.2;color:var(--ink);white-space:nowrap}
.contact svg{flex:none;margin-top:1px}
</style>
</head>
<body>

<!-- Title -->
<section class="slide slide-title col-left row-1">
  <div class="brand" style="left:29px;top:39px">
    <span class="brand-square"></span>
    <span class="brand-name">Dr. Lena Marbach-Voss</span>
  </div>
  <div class="tagline" style="left:29px;top:55px;color:#d3e3f2">Learning that grows teams</div>
  <div class="script-training">training</div>
  <div class="title-line" style="top:108px">Courses, Workshops,</div>
  <div class="title-line" style="top:126px">Consulting<span class="script">and</span></div>
  <div class="coaching">Coaching</div>
  <div class="photo" role="img" aria-label="Smiling businessman in a navy suit with arms crossed" style="left:214px;top:16px;width:160px;height:200px;border-radius:80px 80px 0 0;background:linear-gradient(180deg,#2f4f7a,#1b2f52 70%,#15243f)"></div>
</section>

<!-- Agenda -->
<section class="slide col-right row-1">
  <div class="agenda-word">AGENDA</div>
  <div class="agenda-item" style="left:25px;top:117px"><span class="arrow">↗</span><span><span class="soft">Introduction to</span><br><span class="strong">Our History</span></span></div>
  <div class="agenda-item" style="left:25px;top:146px"><span class="arrow">↗</span><span><span class="soft">Our</span><br><span class="strong">Mission</span></span></div>
  <div class="agenda-item" style="left:117px;top:126px"><span class="arrow">↗</span><span><span class="soft">Our</span><br><span class="strong">Approach</span></span></div>
  <div class="agenda-item" style="left:117px;top:157px"><span class="arrow">↗</span><span><span class="soft">Our Success</span><br><span class="strong">Stories</span></span></div>
  <div class="agenda-item" style="left:207px;top:117px"><span class="arrow">↗</span><span><span class="strong">Services</span><br><span class="soft">We Provide</span></span></div>
  <div class="agenda-item" style="left:207px;top:146px"><span class="arrow">↗</span><span><span class="strong">Key Sectors</span><br><span class="soft">We Serve</span></span></div>
  <div class="agenda-item" style="left:297px;top:126px"><span class="arrow">↗</span><span><span class="soft">Why</span><br><span class="strong">Choose Us</span></span></div>
  <div class="agenda-item" style="left:297px;top:155px"><span class="arrow">↗</span><span><span class="soft">Our</span><br><span class="strong">Team</span></span></div>
</section>

<!-- About Us -->
<section class="slide col-left row-2">
  <div class="abs" style="left:12px;top:13px;width:16px;height:138px;background:var(--steel);border-radius:3px"></div>
  <div class="photo" role="img" aria-label="Presenter at a whiteboard with sticky notes in front of a seated team" style="left:20px;top:21px;width:159px;height:121px;background:linear-gradient(135deg,#e9ecef,#bfc6cf 50%,#6f6258)"></div>
  <div class="card" style="left:73px;top:131px;width:89px;height:65px;background:var(--blue);padding:7px 8px">
    <div class="body white" style="position:static">Lorem ipsum dolor sit amet, consectetur adipiscing elit, sed do eiusmod tempor incididunt ut labore et dolore magna aliqua.</div>
  </div>
  <div class="eyebrow" style="left:209px;top:44px">WHO WE ARE</div>
  <div class="heading" style="left:209px;top:56px;font-size:19px">About Us</div>
  <div class="body bold" style="left:209px;top:86px;width:130px">Lorem ipsum dolor sit amet, consectetur adipiscing elit, sed do eiusmod tempor incididunt ut labore et dolore magna</div>
  <div class="body" style="left:209px;top:117px;width:135px">Lorem ipsum dolor sit amet, consectetur adipiscing elit, sed do eiusmod tempor incididunt ut labore et dolore magna aliqua. Quis ipsum suspendisse ultrices gravida. Risus commodo viverra maecenas</div>
</section>

<!-- Mission & Vision -->
<section class="slide col-right row-2">
  <div class="eyebrow" style="left:22px;top:29px">WHO WE DO</div>
  <div class="heading" style="left:22px;top:41px">Mission &amp; Our Vision</div>
  <div class="body dark" style="left:24px;top:70px;width:178px">Lorem ipsum dolor sit amet, consectetur adipiscing elit, sed do eiusmod tempor incididunt ut labore et dolore magna aliqua.</div>
  <div class="body" style="left:216px;top:23px;width:130px">Lorem ipsum dolor sit amet, consectetur adipiscing elit, sed do eiusmod tempor incididunt ut labore et dolore magna</div>
  <div class="abs" style="left:216px;top:58px;width:37px;height:46px;border:4px solid var(--steel);border-right:none;border-radius:4px 0 0 4px"></div>
  <div class="card" style="left:220px;top:61px;width:140px;height:40px;background:#f1f3f5;padding:8px 10px">
    <div class="body" style="position:static;width:98px">Lorem ipsum dolor sit amet, consectetur adipiscing elit, sed do eiusmod tempor</div>
  </div>
  <div class="pct-pill">45%</div>
  <div class="icon-tile" style="left:24px;top:113px;background:var(--blue)">
    <svg width="12" height="10" viewBox="0 0 12 10" fill="none" stroke="#fff" stroke-width="1"><path d="M1 9.5h10M2.5 9V5M5 9V3M7.5 9V6M10 9V4M1 3l3-2 3 2 4-2"/></svg>
  </div>
  <div class="icon-tile" style="left:123px;top:113px;background:var(--steel)">
    <svg width="12" height="12" viewBox="0 0 12 12" fill="none" stroke="#fff" stroke-width="1"><circle cx="6" cy="6" r="4.5"/><circle cx="6" cy="6" r="2"/><path d="M6 6l4-4"/></svg>
  </div>
  <div class="card" style="left:19px;top:132px;width:89px;height:66px;background:#f3f4f6">
    <div class="body" style="position:static">Lorem ipsum dolor sit amet, consectetur adipiscing elit, sed do eiusmod tempor incididunt ut labore et dolore magna aliqua.</div>
  </div>
  <div class="card" style="left:116px;top:132px;width:94px;height:66px;background:#000">
    <div class="body white" style="position:static">Lorem ipsum dolor sit amet, consectetur adipiscing elit, sed do eiusmod tempor incididunt ut labore et dolore magna aliqua.</div>
  </div>
  <div class="photo" role="img" aria-label="Audience in a conference hall listening to a speaker" style="left:216px;top:116px;width:143px;height:81px;background:linear-gradient(180deg,#c77a3e,#7a4a2c 45%,#3a2a26)"></div>
</section>

<!-- Our Approach -->
<section class="slide col-left row-3">
  <div class="eyebrow" style="left:24px;top:29px">HOW WE WORK</div>
  <div class="heading" style="left:24px;top:41px">Our Approach</div>
  <div class="body dark" style="left:25px;top:71px;width:125px">Lorem ipsum dolor sit amet, consectetur adipiscing elit, sed do eiusmod tempor incididunt ut labore et dolore magna.</div>
  <div class="photo" role="img" aria-label="Team meeting around a table with documents and laptops" style="left:24px;top:110px;width:114px;height:79px;background:linear-gradient(135deg,#5b5149,#8b7968 50%,#3e3a38)"></div>
  <div class="title-sm" style="left:168px;top:46px;font-weight:400">Tailored<br>Solutions</div>
  <svg class="abs" style="left:229px;top:44px" width="20" height="20" viewBox="0 0 20 20" fill="none" stroke="var(--blue)" stroke-width=".9"><circle cx="10" cy="8" r="4"/><path d="M10 12v7M7 19h6M10 1v2M3 8H1M19 8h-2M4.5 2.5l1.5 1.5M15.5 2.5L14 4"/></svg>
  <div class="body" style="left:168px;top:67px;width:80px">Every project is unique. We customize strategies to meet local needs and priorities.</div>
  <div class="card" style="left:266px;top:37px;width:98px;height:64px;background:var(--blue);padding:7px 8px">
    <div class="body white" style="position:static">Lorem ipsum dolor sit amet, consectetur adipiscing elit, sed do eiusmod tempor incididunt ut labore et dolore magna aliqua.</div>
  </div>
  <div class="card" style="left:160px;top:110px;width:97px;height:70px;background:#f3f4f6">
    <div class="title-sm" style="position:static;font-weight:400">Collaborative<br>Partnerships</div>
    <div class="body" style="position:static;margin-top:3px">We work closely with governments, NGOs, and private sector players to drive success.</div>
  </div>
  <svg class="abs" style="left:235px;top:115px" width="16" height="18" viewBox="0 0 16 18" fill="none" stroke="var(--blue)" stroke-width=".9"><circle cx="8" cy="10" r="6.5"/><path d="M4 10l3 2 5-5M8 1v2"/></svg>
  <div class="card" style="left:266px;top:110px;width:98px;height:70px;background:#fff;border:1px solid #d5d9de">
    <div class="title-sm" style="position:static;font-weight:400">Data-Driven<br>Decisions</div>
    <div class="body" style="position:static;margin-top:3px">We work closely with governments, NGOs, and private sector players to drive success.</div>
  </div>
  <svg class="abs" style="left:340px;top:115px" width="20" height="18" viewBox="0 0 20 18" fill="none" stroke="var(--blue)" stroke-width=".9"><circle cx="10" cy="8" r="4"/><circle cx="5" cy="14" r="2.5"/><path d="M1 5h6M13 5h6M10 1v3"/></svg>
</section>

<!-- Success Stories -->
<section class="slide col-right row-3">
  <div class="eyebrow" style="left:24px;top:25px">OUR</div>
  <div class="heading" style="left:24px;top:35px">Success Stories</div>
  <svg class="abs" style="left:0;top:0" width="383" height="216" viewBox="0 0 383 216" font-family="Plus Jakarta Sans, sans-serif" font-size="4.5" fill="#333">
    <g stroke="#dde1e6" stroke-width=".6">
      <line x1="48" y1="82" x2="48" y2="193"/><line x1="77" y1="82" x2="77" y2="193"/><line x1="106" y1="82" x2="106" y2="193"/><line x1="136" y1="82" x2="136" y2="193"/><line x1="165" y1="82" x2="165" y2="193"/>
    </g>
    <g stroke="#222" stroke-width=".7">
      <line x1="31" y1="82" x2="31" y2="193"/><line x1="31" y1="193" x2="168" y2="193"/>
      <line x1="28" y1="83" x2="34" y2="83"/><line x1="28" y1="105" x2="34" y2="105"/><line x1="28" y1="127" x2="34" y2="127"/><line x1="28" y1="149" x2="34" y2="149"/><line x1="28" y1="171" x2="34" y2="171"/>
    </g>
    <g text-anchor="end"><text x="25" y="85">60</text><text x="25" y="107">50</text><text x="25" y="129">40</text><text x="25" y="151">30</text><text x="25" y="173">20</text><text x="25" y="195">0</text></g>
    <g text-anchor="middle"><text x="48" y="203">1</text><text x="77" y="203">2</text><text x="106" y="203">3</text><text x="136" y="203">4</text><text x="165" y="203">5</text></g>
    <path d="M38 160 C45 161 60 150 77 146 S97 135 106 135 S128 134 136 138 S158 146 165 152" fill="none" stroke="#c3ccd6" stroke-width="1.2"/>
    <path d="M38 164 C45 166 60 159 77 156 S96 149 106 149 S128 150 136 153 S158 162 165 168" fill="none" stroke="var(--blue)" stroke-width="1.2"/>
    <g fill="#fff" stroke="var(--blue)" stroke-width=".9">
      <circle cx="48" cy="155" r="1.8"/><circle cx="48" cy="160" r="1.8"/><circle cx="48" cy="163" r="1.8"/>
      <circle cx="77" cy="137" r="1.8"/><circle cx="77" cy="146" r="1.8"/><circle cx="77" cy="156" r="1.8"/>
      <circle cx="106" cy="122" r="1.8"/><circle cx="106" cy="135" r="1.8"/><circle cx="106" cy="149" r="1.8"/>
      <circle cx="136" cy="124" r="1.8"/><circle cx="136" cy="138" r="1.8"/><circle cx="136" cy="153" r="1.8"/>
      <circle cx="165" cy="139" r="1.8"/><circle cx="165" cy="152" r="1.8"/><circle cx="165" cy="168" r="1.8"/>
    </g>
    <g fill="none" stroke-width="1.3" stroke="var(--blue)">
      <circle cx="209" cy="70" r="13" stroke="#e3e7ec"/><circle cx="209" cy="70" r="13" stroke-dasharray="61.3 81.7" transform="rotate(-90 209 70)"/>
      <circle cx="209" cy="118" r="13" stroke="#e3e7ec"/><circle cx="209" cy="118" r="13" stroke-dasharray="40.8 81.7" transform="rotate(90 209 118)"/>
      <circle cx="209" cy="164" r="13" stroke="#e3e7ec"/><circle cx="209" cy="164" r="13" stroke-dasharray="20.4 81.7" transform="rotate(90 209 164)"/>
    </g>
    <g text-anchor="middle" fill="var(--blue)" font-size="5"><text x="209" y="72">75%</text><text x="209" y="120">50%</text><text x="209" y="166">25%</text></g>
  </svg>
  <div class="title-sm" style="left:233px;top:49px;font-weight:400">Lorem Ipsum</div>
  <div class="body" style="left:233px;top:60px;width:100px">Lorem ipsum dolor sit amet, consectetur adipiscing elit, sed do eiusmod tempor</div>
  <div class="title-sm" style="left:233px;top:97px;font-weight:400">Lorem Ipsum</div>
  <div class="body" style="left:233px;top:108px;width:100px">Lorem ipsum dolor sit amet, consectetur adipiscing elit, sed do eiusmod tempor</div>
  <div class="title-sm" style="left:233px;top:146px;font-weight:400">Lorem Ipsum</div>
  <div class="body" style="left:233px;top:157px;width:100px">Lorem ipsum dolor sit amet, consectetur adipiscing elit, sed do eiusmod tempor</div>
</section>

<!-- Key Sectors -->
<section class="slide col-left row-4">
  <div class="abs" style="left:0;top:0;width:126px;height:216px;background:var(--panel)"></div>
  <div class="eyebrow plain" style="left:24px;top:69px">KEY SECTORS</div>
  <div class="heading" style="left:24px;top:80px">We Serve</div>
  <div class="abs" style="left:62px;top:102px;width:36px;height:1px;background:var(--steel-light)"></div>
  <div class="body dark" style="left:24px;top:114px;width:92px">Lorem ipsum dolor sit amet, consectetur adipiscing elit, sed do eiusmod tempor incididunt ut labore et</div>
  <svg class="abs" style="left:0;top:0" width="383" height="216" viewBox="0 0 383 216" fill="none">
    <circle cx="238" cy="95" r="30" stroke="#e6e9ed" stroke-width=".6"/>
    <circle cx="238" cy="95" r="30" stroke="var(--ring-grey)" stroke-width="4.5" stroke-dasharray="110 188.5" transform="rotate(95 238 95)"/>
    <circle cx="298" cy="95" r="30" stroke="#e6e9ed" stroke-width=".6"/>
    <circle cx="298" cy="95" r="30" stroke="var(--blue)" stroke-width="5" stroke-dasharray="120 188.5" transform="rotate(-80 298 95)"/>
    <circle cx="238" cy="156" r="30" stroke="#e6e9ed" stroke-width=".6"/>
    <circle cx="238" cy="156" r="30" stroke="var(--steel)" stroke-width="4.5" stroke-dasharray="110 188.5" transform="rotate(-85 238 156)"/>
    <g stroke="#222" stroke-width=".8">
      <circle cx="143" cy="40" r="4"/><path d="M139 52h16M141 51v-4M144 51v-6M147 51v-3M150 51v-5M153 51v-7M149 39l3-2 3 2"/>
      <rect x="271" y="26" width="16" height="10" rx="1"/><path d="M274 33l3-3 3 2 4-3M271 40h6M280 40h7"/>
      <rect x="336" y="137" width="12" height="10"/><path d="M338 140h8M338 143h8M347 146l5-3v6z"/>
    </g>
  </svg>
  <div class="title-sm" style="left:238px;top:87px;transform:translateX(-50%);text-align:center;font-weight:400">Lorem<br>Ipsum</div>
  <div class="title-sm" style="left:298px;top:87px;transform:translateX(-50%);text-align:center;font-weight:400">Lorem<br>Ipsum</div>
  <div class="title-sm" style="left:238px;top:148px;transform:translateX(-50%);text-align:center;font-weight:400">Lorem<br>Ipsum</div>
  <div class="body" style="left:137px;top:56px;width:68px">Lorem ipsum dolor sit amet, consectetur adipiscing elit, sed do eiusmod tempor</div>
  <div class="body" style="left:295px;top:27px;width:70px">Lorem ipsum dolor sit amet, consectetur adipiscing elit, sed do eiusmod tempor</div>
  <div class="body" style="left:282px;top:157px;width:70px">Lorem ipsum dolor sit amet, consectetur adipiscing elit, sed do eiusmod tempor</div>
</section>

<!-- Why Choose Us -->
<section class="slide col-right row-4">
  <div class="abs" style="left:151px;top:26px;width:23px;height:1px;background:var(--steel-light)"></div>
  <div class="abs center" style="top:20px;font-size:9.5px">WHY</div>
  <div class="abs" style="left:208px;top:26px;width:23px;height:1px;background:var(--steel-light)"></div>
  <div class="heading center" style="top:30px;text-align:center">Choos Us</div>
  <div class="body dark center" style="top:56px;padding:0 82px;text-align:center">Lorem ipsum dolor sit amet, consectetur adipiscing elit, sed do eiusmod tempor incididunt ut labore et dolore magna. aliqua. Quis ipsum</div>
  <div class="pill">Lorem ipsum dolor sit amet, consectetur</div>
  <svg class="abs" style="left:0;top:0" width="383" height="216" viewBox="0 0 383 216">
    <line x1="75" y1="112" x2="307" y2="112" stroke="var(--steel)" stroke-width=".7" stroke-dasharray="1.5 1.5"/>
    <circle cx="75" cy="112" r="2" fill="var(--steel)"/><circle cx="191" cy="112" r="2" fill="var(--steel)"/><circle cx="307" cy="112" r="2" fill="var(--steel)"/>
  </svg>
  <div class="feature-dot" style="left:64px;top:126px"><svg width="9" height="9" viewBox="0 0 9 9" fill="none" stroke="#fff" stroke-width=".8"><rect x="1" y="1" width="6" height="7"/><path d="M3 6l4-4"/></svg></div>
  <div class="feature-dot" style="left:180px;top:126px"><svg width="9" height="9" viewBox="0 0 9 9" fill="none" stroke="#fff" stroke-width=".8"><circle cx="4" cy="4" r="3"/><path d="M6 6l2.5 2.5"/></svg></div>
  <div class="feature-dot" style="left:296px;top:126px"><svg width="9" height="9" viewBox="0 0 9 9" fill="none" stroke="#fff" stroke-width=".8"><path d="M4.5 .5c2 2 2 5 0 7-2-2-2-5 0-7zM3 7l-1 1.5M6 7l1 1.5"/></svg></div>
  <div class="feature" style="left:27px;top:160px"><div class="title-sm" style="font-weight:400">Lorem Ipsum</div><div class="body">Lorem ipsum dolor sit amet, consectetur adipiscing elit, sed do eiusmod tempor</div></div>
  <div class="feature" style="left:143px;top:160px"><div class="title-sm" style="font-weight:400">Lorem Ipsum</div><div class="body">Lorem ipsum dolor sit amet, consectetur adipiscing elit, sed do eiusmod tempor</div></div>
  <div class="feature" style="left:258px;top:160px"><div class="title-sm" style="font-weight:400">Lorem Ipsum</div><div class="body">Lorem ipsum dolor sit amet, consectetur adipiscing elit, sed do eiusmod tempor</div></div>
</section>

<!-- Break Slide -->
<section class="slide slide-break col-left row-5">
  <div class="photo" role="img" aria-label="Two business colleagues looking at a tablet together" style="left:13px;top:13px;width:174px;height:203px;border-radius:80px 80px 0 0;background:linear-gradient(180deg,#6b7b92,#2c3e5c 55%,#1a2a45)"></div>
  <div class="heading" style="left:201px;top:64px;color:var(--white)">Break Slide</div>
  <div class="body white" style="left:201px;top:90px;width:125px">Lorem ipsum dolor sit amet, consectetur adipiscing elit, sed do eiusmod tempor incididunt ut labore et dolore magna.</div>
  <div class="abs" style="left:202px;top:124px;width:1px;height:37px;background:var(--steel-light)"></div>
  <div class="title-sm" style="left:211px;top:125px;color:var(--white);font-weight:400">Lorem Ipsum</div>
  <div class="body" style="left:211px;top:136px;width:100px;color:#b9d4ec">Lorem ipsum dolor sit amet, consectetur adipiscing elit, sed do eiusmod tempor</div>
</section>

<!-- Closing -->
<section class="slide slide-close col-right row-5">
  <div class="brand" style="left:121px;top:36px;color:var(--blue)">
    <span class="brand-square"></span>
    <span class="brand-name">Dr. Lena Marbach-Voss</span>
  </div>
  <div class="tagline" style="left:121px;top:52px;color:#6f8ea8">Learning that grows teams</div>
  <div class="thanks">Thank you!</div>
  <div class="body dark center" style="top:130px;font-size:7.2px;text-align:center">Lorem ipsum dolor sit amet, consectetur<br>adipiscing elit, sed do eiusmod tempor.</div>
  <div class="contact" style="left:112px;top:156px">
    <svg width="7" height="7" viewBox="0 0 7 7"><path d="M1.5.3l1.2 1.5-.7.9c.4.9 1.2 1.7 2.1 2.1l.9-.7 1.5 1.2-.7 1.2C3.3 6.4.6 3.7.3 1z" fill="var(--blue)"/></svg>
    <span>(+1) 555 014 2086</span>
  </div>
  <div class="contact" style="left:202px;top:156px">
    <svg width="7" height="6" viewBox="0 0 7 6"><rect x=".3" y=".5" width="6.4" height="5" fill="var(--blue)"/><path d="M.5 .8L3.5 3.3 6.5 .8" stroke="#fff" stroke-width=".6" fill="none"/></svg>
    <span>info@northlea.com</span>
  </div>
  <div class="contact" style="left:112px;top:170px">
    <svg width="6" height="8" viewBox="0 0 6 8"><path d="M3 .3a2.6 2.6 0 0 1 2.6 2.6C5.6 4.8 3 7.7 3 7.7S.4 4.8.4 2.9A2.6 2.6 0 0 1 3 .3z" fill="var(--blue)"/><circle cx="3" cy="2.9" r=".9" fill="#fff"/></svg>
    <span style="font-size:6.6px;color:#444">Lorem ipsum dolor<br>sit amet, City, USA.</span>
  </div>
  <div class="contact" style="left:202px;top:170px">
    <svg width="6" height="7" viewBox="0 0 6 7"><path d="M.5.3l5 3-2.1.5-.9 2.3z" fill="var(--blue)"/></svg>
    <span>www.northlea.com</span>
  </div>
</section>

</body>
</html>
```